Call Center In Need of Website Design

We are a call center that provides inbound and outbound calling & marketing services for eCommerce store. We would like to see a fun, creative, playful design that is simple.

Here are some sample design sites we like;
- https://www.velmoreline.com/
- https://pindrask.io/
- https://www.glimbertic.com/live-chat-software/
- https://www.zavrolin.com/

Here are some competitor sites;
- https://www.ostrevaglinks.com/
- https://www.helpkestrel.com/

I have attached website content for your use.

Target Market(s)

eCommerce

Coding

Coded - Design and coding required

Number of Pages Required

5+ page

Font styles to use
Sans Serif

Colors

Designer to choose colors to be used in the design.

Requirements
Must have
• Must have designs for the following 5 separate pages;
• 1. Home (landing)
• - This will be were the design style really needs to show.
• - Just needs to touch on key services
• - CTA
• 2. About Us
• - Basic page for about me paragraph
• 3. Services
• - List of services with icons
• - Click on service type to expand details or hover over service icon to view popup bubble with details about that service
• 4. Pricing
• - Option to bundle 1(one) digital service plan and 1(one) call center service plan
• - Bundling adds 10% monthly discount to over all price
• - Customer does NOT have to bundle
• - FAQ
• 5. Contact Us
• - Include a capture form (name, company name, email, phone, message)
• - Contact info
• - Business hours
• When customer purchases their desired plan, then they are taken to a page where they must schedule a call with an account rep.
Nice to have
• home page animations
Should not have
• All information on Home/Landing page.

```html
<!DOCTYPE html>
<html lang="en">
<head>
<meta charset="utf-8">
<title>Tellvane — Call Center for eCommerce</title>
<link href="https://fonts.googleapis.com/css2?family=Open+Sans:wght@400;600;700;800&display=swap" rel="stylesheet">
<style>
:root{
  --teal:#58bc9c;
  --teal-soft:#bfe5d8;
  --ink:#222222;
  --text:#444444;
  --muted:#777777;
  --line:#d9d9d9;
  --white:#ffffff;
  --dark-btn:#2b2f33;
}
*{box-sizing:border-box;margin:0;padding:0}
html,body{width:1200px;height:2875px;overflow:hidden;background:var(--white)}
body{font-family:'Open Sans',sans-serif;color:var(--text);position:relative}
.abs{position:absolute}

/* header */
.site-header{position:absolute;left:0;top:0;width:1200px;height:90px;display:flex;align-items:center}
.brand{position:absolute;left:75px;top:26px;display:flex;align-items:center;gap:12px}
.brand-dot{width:36px;height:36px;border-radius:50%;border:3px solid var(--teal)}
.brand-name{font-size:26px;font-weight:400;letter-spacing:5px;color:#555}
.main-nav{position:absolute;left:498px;top:36px;display:flex;gap:40px;font-size:15px;color:#333}
.main-nav .active{color:var(--teal)}
.header-social{position:absolute;left:995px;top:37px;display:flex;gap:16px;align-items:center}
.header-social .dot{width:13px;height:13px;border-radius:50%;background:#333}

/* hero */
.hero{position:absolute;left:0;top:90px;width:1200px;height:587px;
  background:linear-gradient(90deg,#dbe4ec 0%,#c7d6e2 45%,#b9cbd9 70%,#e2b64a 100%)}
.hero-photo{position:absolute;right:0;top:0;width:560px;height:587px;
  background:radial-gradient(ellipse at 55% 40%,#d8b9a4 0%,#9a7560 35%,rgba(185,203,217,0) 65%),linear-gradient(180deg,rgba(0,0,0,0) 70%,#f2b632 100%)}
.hero-title{position:absolute;left:201px;top:318px;font-size:34px;font-weight:700;color:var(--ink)}
.hero-sub{position:absolute;left:201px;top:368px;width:430px;font-size:16px;line-height:22px;color:#333}
.btn-dark{position:absolute;left:201px;top:435px;width:225px;height:41px;background:var(--dark-btn);border-radius:3px;
  color:var(--teal-soft);font-weight:700;font-size:17px;display:flex;align-items:center;justify-content:center;gap:14px}
.hero-arrow{position:absolute;top:372px}

/* partners */
.partners{position:absolute;left:0;top:677px;width:1200px;height:109px;border-bottom:1px solid #eee;
  display:flex;align-items:center;justify-content:space-between;padding:0 72px}
.partner{display:flex;align-items:center;gap:8px;font-size:27px;font-weight:700;color:#222}
.partner .sq{width:22px;height:22px;background:#5e8e3e}

/* sections */
.section-title{position:absolute;left:0;width:1200px;text-align:center;font-size:33px;font-weight:700;color:var(--ink)}
.section-text{position:absolute;left:180px;width:840px;text-align:center;font-size:14.5px;line-height:24px;color:#444}
.btn-teal{position:absolute;background:var(--teal);color:#1f3d33;font-weight:700;font-size:17px;border-radius:3px;
  display:flex;align-items:center;justify-content:center}
.rule{position:absolute;height:2px;background:var(--teal-soft)}
.rule-dark{position:absolute;height:1px;background:#555}
.services-heading{position:absolute;left:0;top:1253px;width:1200px;text-align:center;font-size:29px;font-weight:700;color:var(--ink)}

.photo{position:absolute}
.svc-title{position:absolute;font-size:22px;font-weight:700;color:var(--ink)}
.svc-list{position:absolute;list-style:none;font-size:15px;color:#333}
.svc-list li{height:33px;display:flex;align-items:center;gap:18px}
.svc-list li::before{content:"";width:0;height:0;border-left:6px solid #333;border-top:4px solid transparent;border-bottom:4px solid transparent}

/* contact band */
.contact-band{position:absolute;left:0;top:2132px;width:1200px;height:410px;
  background:linear-gradient(90deg,#e4e6e8 0%,#d4d6d8 40%,#bfc2c4 70%,#cfc4b8 100%)}
.contact-form{position:absolute;left:75px;top:2151px;width:379px;height:489px;background:var(--white);border:1px solid #cfcfcf;border-radius:3px}
.field{position:absolute;left:39px;width:300px;border-bottom:1px solid #999;font-size:15px;color:#222;padding-bottom:12px}
.btn-send{left:137px;top:416px;width:104px;height:38px;font-size:15px;color:#fff;gap:10px}

/* footer */
.footer-brand{position:absolute;left:146px;top:2668px;display:flex;align-items:center;gap:12px}
.footer-social{position:absolute;left:142px;top:2735px;display:flex;gap:12px}
.footer-social span{width:40px;height:40px;border-radius:50%}
.copyright{position:absolute;left:136px;top:2792px;font-size:13px;color:#333}
.copyright b{font-size:15px;margin-left:6px}
.footer-title{position:absolute;font-size:22px;color:#222}
.footer-list{position:absolute;list-style:none;font-size:15px;color:#333}
.footer-list li{height:28px;display:flex;align-items:center;gap:18px}
.quick li::before{content:"";border-left:5px solid #333;border-top:4px solid transparent;border-bottom:4px solid transparent}
.version{position:absolute;left:1146px;top:2820px;font-size:13px;font-weight:700;color:#333}
</style>
</head>
<body>

<header class="site-header">
  <div class="brand"><span class="brand-dot"></span><span class="brand-name">TELLVANE</span></div>
  <nav class="main-nav">
    <span class="active">HOME</span><span>ABOUT</span><span>SERVICES</span><span>PRICING</span><span>CONTACT US</span>
  </nav>
  <div class="header-social">
    <span class="dot"></span><span class="dot"></span><span class="dot"></span>
    <svg width="16" height="12" viewBox="0 0 16 12"><rect x="1" y="1" width="14" height="10" fill="none" stroke="#333" stroke-width="2"/><path d="M1 1l7 6 7-6" fill="none" stroke="#333" stroke-width="2"/></svg>
  </div>
</header>

<section class="hero">
  <div class="hero-photo" role="img" aria-label="Smiling call center agent wearing a headset and yellow top"></div>
</section>
<svg class="hero-arrow" style="left:118px" width="20" height="30" viewBox="0 0 20 30"><path d="M16 3L4 15l12 12" fill="none" stroke="#fff" stroke-width="4"/></svg>
<svg class="hero-arrow" style="left:1068px" width="20" height="30" viewBox="0 0 20 30"><path d="M4 3l12 12L4 27" fill="none" stroke="#fff" stroke-width="4"/></svg>
<h1 class="hero-title">WE ARE A CALL CENTER</h1>
<p class="hero-sub">That provides inbound and outbound calling &amp; marketing services for eCommerce store.</p>
<div class="btn-dark">PLAN &amp; PRICING
  <svg width="22" height="12" viewBox="0 0 22 12"><path d="M0 6h18M13 1l6 5-6 5" fill="none" stroke="#bfe5d8" stroke-width="2.5"/></svg>
</div>

<div class="partners">
  <span class="partner"><span class="sq"></span>Cartwell</span>
  <span class="partner">Pagemint</span>
  <span class="partner">Rivermart</span>
  <span class="partner">Storelyx</span>
  <span class="partner">Paylumo</span>
  <span class="partner">Shopnestly</span>
</div>

<h2 class="section-title" style="top:818px">WELCOME</h2>
<p class="section-text" style="top:868px">Maecenas pellentesque enim neque mi sed. Maecenas turpis neque blandit wisi fermentum congue at vivamus pharetra at placerat. Urna volutpat vitae nunc con eget. Mus sit mauris magna commodo lacus lorem pellentesque tempus. Fringilla duis habitant lacinia lorem eros tortor sed a. Repellendus nunc maxime.</p>
<div class="rule" style="left:327px;top:1000px;width:170px"></div>
<div class="btn-teal" style="left:515px;top:980px;width:170px;height:41px">READ MORE</div>
<div class="rule" style="left:703px;top:1000px;width:170px"></div>

<h2 class="section-title" style="top:1078px">WHAT WE DO?</h2>
<p class="section-text" style="top:1128px">Tellvane is your personal customer service and product research team. We love eCommerce, but we love seeing business owners succeed even more! That is exactly why we have developed the processes and technology to take care of the most over looked areas in eCommerce -Customer Service andRetention.<br><b style="color:#222">Let Tellvane handle your customers while you focus on growing your business.</b></p>

<div class="rule-dark" style="left:398px;top:1275px;width:128px"></div>
<h2 class="services-heading">Services</h2>
<div class="rule-dark" style="left:675px;top:1275px;width:128px"></div>

<div class="photo" style="left:75px;top:1319px;width:513px;height:320px;background:linear-gradient(180deg,#0d1420 0%,#22344e 50%,#0a0f18 100%)" role="img" aria-label="Technician with laptop walking through a server room aisle"></div>
<h3 class="svc-title" style="left:644px;top:1327px">Digital Services</h3>
<ul class="svc-list" style="left:644px;top:1372px">
  <li>Email Support</li><li>Live Chat Support</li><li>Product Research</li><li>Product Listing</li><li>Price Monitoring</li><li>Product Photo &amp; Video Editing</li>
</ul>
<div class="btn-teal" style="left:646px;top:1595px;width:150px;height:40px">VIEW PRICING</div>

<h3 class="svc-title" style="left:77px;top:1714px">Call Center Services</h3>
<ul class="svc-list" style="left:75px;top:1758px">
  <li>Answering service</li><li>Welcome Calls</li><li>Follow-Up Service</li><li>Customer Upselling</li><li>Over-The-Phone Order Taking</li><li>Order Return Processing</li>
</ul>
<ul class="svc-list" style="left:345px;top:1758px">
  <li>Feedback/Survey Calls</li><li>Message Delivering Service</li><li>ROI Diagnostics &amp;Reporting</li><li>Scalable Call Center Pricing</li><li>Customizable ForAny Industry</li><li>100% US-Based Agents</li>
</ul>
<div class="btn-teal" style="left:77px;top:1975px;width:150px;height:40px">VIEW PRICING</div>
<div class="photo" style="left:613px;top:1720px;width:514px;height:318px;background:linear-gradient(90deg,#6a4a3a 0%,#c49a86 45%,#e6e3df 75%,#f4f2ef 100%)" role="img" aria-label="Smiling call center agent with headset, colleagues blurred behind"></div>

<section class="contact-band" role="img" aria-label="Team of smiling call center agents with headsets in an office"></section>
<form class="contact-form">
  <div class="field" style="top:42px">Name</div>
  <div class="field" style="top:107px">Company name</div>
  <div class="field" style="top:173px">Email</div>
  <div class="field" style="top:232px">Phone</div>
  <div class="field" style="top:285px;height:97px">Message</div>
  <div class="btn-teal btn-send">SEND
    <svg width="7" height="11" viewBox="0 0 7 11"><path d="M1 1l4.5 4.5L1 10" fill="none" stroke="#fff" stroke-width="2"/></svg>
  </div>
</form>

<footer>
  <div class="footer-brand"><span class="brand-dot"></span><span class="brand-name">TELLVANE</span></div>
  <div class="footer-social">
    <span style="background:#3b5a99"></span><span style="background:#3d9ad9"></span><span style="background:#d8423a"></span><span style="background:#8a3ab0"></span><span style="background:#2d6fa6"></span>
  </div>
  <p class="copyright">© 2018 | <b>www.tellvane.com</b></p>

  <h4 class="footer-title" style="left:587px;top:2598px">Contact Us</h4>
  <ul class="footer-list" style="left:587px;top:2642px">
    <li><svg width="10" height="14" viewBox="0 0 10 14"><path d="M5 0a5 5 0 0 1 5 5c0 4-5 9-5 9S0 9 0 5a5 5 0 0 1 5-5z" fill="#333"/><circle cx="5" cy="5" r="2" fill="#fff"/></svg><span style="margin-left:8px">Tellvane, Inc.</span></li>
    <li style="padding-left:36px">418 Calder Row</li>
    <li style="padding-left:36px">Marlow, CA 90412</li>
    <li><svg width="12" height="12" viewBox="0 0 24 24"><path d="M6.6 10.8a15 15 0 0 0 6.6 6.6l2.2-2.2c.3-.3.7-.4 1-.2 1.1.4 2.3.6 3.6.6.6 0 1 .4 1 1V20c0 .6-.4 1-1 1A17 17 0 0 1 3 4c0-.6.4-1 1-1h3.5c.6 0 1 .4 1 1 0 1.2.2 2.4.6 3.6.1.3 0 .7-.2 1z" fill="#333"/></svg><span style="margin-left:6px">(800) 555-0147</span></li>
  </ul>

  <h4 class="footer-title" style="left:884px;top:2598px">Quick Links</h4>
  <ul class="footer-list quick" style="left:884px;top:2642px">
    <li>Home</li><li>About</li><li>Services</li><li>Pricing</li><li>Contact Us</li>
  </ul>
  <span class="version">M1</span>
</footer>

</body>
</html>
```